Financial Advisor Resource Firm needs business card design

Need business card design for company in Omaha NE called Meridale Circle. We provide resources to financial advisors....workshop programs, retirement analysis, and insurance planning. I would like to see designs that use grays, greens, black, and white colors. The final design should communicate 'collaboration' and be simple yet attractive to financial planning clients. I will attached our logo and another picture of a puzzle piece coming together. I would like the incorporate the puzzle picture somehow, maybe on the back somehow, with color or just the gray scale....OR, the picture be the front of the card with 'Meridale' definition on it (see upload) and then company logo, employee name, title, address on the back (see ppt uploaded). The following disclosure needs to be included somewhere- Advisory services offered through Stonebrook Assets, LLC.
Updates

I uploaded a svg and ai file of the logo

Target Market(s)

Financial planning clients and financial advisors....so pretty diverse age range of about 40-70.

Industry/Entity Type

Financial Planning

Contact Information for Business Card

Tobias L. Fenwright, MBA
Founder/President
5287 E. Larkin Road
Suite 410
Harlow, NE 68190
Phone- (402) 555-0147
Cell- (402) 555-0183
Fax- (402) 555-0129
email- tobias@meridaleplan.example
web address- www.meridaleplan.example

Colors
1b1b1b
474747
d3d3d3
ffffff
9bcb3c
abd036

Requirements
Must have
• Must include logo provided, must be 2 sided, and must have disclosure...all of these items listed in project description

```html
<!DOCTYPE html>
<html lang="en">
<head>
<meta charset="utf-8">
<title>Meridale Circle – Business Card</title>
<link rel="stylesheet" href="https://fonts.googleapis.com/css2?family=Arimo:wght@400;700&display=swap">
<style>
  :root {
    --green: #9bcb3c;
    --green-light: #abd036;
    --green-deep: #7fb33a;
    --ink: #1b1b1b;
    --graphite: #474747;
    --silver: #d3d3d3;
    --paper: #ffffff;
    --backdrop: #ecece8;
  }
  * { box-sizing: border-box; margin: 0; padding: 0; }
  html, body {
    width: 1200px; height: 900px; overflow: hidden;
    background: var(--backdrop);
    font-family: "Arimo", Arial, sans-serif;
  }
  .canvas {
    width: 1200px; height: 900px;
    display: flex; flex-direction: column;
    align-items: center; justify-content: center; gap: 40px;
  }
  .card {
    position: relative;
    width: 700px; height: 400px;
    border-radius: 4px; overflow: hidden;
    box-shadow: 0 6px 18px rgba(0,0,0,.15);
  }

  /* Back side */
  .card-back { background: var(--green); }
  .card-back .photo-area {
    position: absolute; inset: 0;
    background: radial-gradient(ellipse at 65% 55%, #b4dc7a 0%, #9bcb3c 45%, #7fb33a 100%);
  }
  .card-back .brand {
    position: absolute; left: 0; right: 0; top: 150px;
    display: flex; align-items: center; justify-content: center; gap: 16px;
  }
  .brand-dot {
    width: 34px; height: 34px; border-radius: 50%;
    border: 4px solid var(--paper);
  }
  .brand-name {
    color: var(--paper); font-weight: 400;
    font-size: 44px; letter-spacing: 4px; text-transform: uppercase;
  }
  .disclosure {
    position: absolute; left: 0; right: 0; top: 250px;
    text-align: center; color: var(--paper);
    font-size: 15px; letter-spacing: .3px;
  }

  /* Front side */
  .card-front { background: var(--paper); }
  .holder { position: absolute; left: 48px; top: 44px; }
  .holder-name {
    color: var(--green); font-weight: 700; font-size: 25px; letter-spacing: .5px;
    text-transform: uppercase;
  }
  .holder-title { color: var(--graphite); font-size: 15px; margin-top: 4px; }
  .contact-band {
    position: absolute; left: 0; top: 112px;
    width: 500px; height: 200px;
    background: linear-gradient(90deg, var(--green) 0%, var(--green-light) 100%);
    padding: 30px 0 0 48px;
  }
  .contact-list { list-style: none; }
  .contact-list li {
    display: flex; align-items: center; gap: 10px;
    color: var(--paper); font-size: 17px; line-height: 27px;
  }
  .contact-list svg { width: 13px; height: 13px; flex: none; }
  .front-brand {
    position: absolute; right: 36px; top: 158px; width: 160px;
    display: flex; flex-direction: column; align-items: center; gap: 12px;
  }
  .front-brand .brand-dot { width: 58px; height: 58px; border: 7px solid var(--green); }
  .front-brand .brand-name {
    color: var(--ink); font-size: 17px; letter-spacing: 2px; text-align: center;
  }
  .address {
    position: absolute; left: 48px; bottom: 40px;
    color: var(--graphite); font-size: 17px;
  }
</style>
</head>
<body>
<main class="canvas">

  <section class="card card-back" aria-label="Card back">
    <div class="photo-area" role="img" aria-label="Green-tinted photograph of hands fitting puzzle pieces together"></div>
    <div class="brand">
      <span class="brand-dot"></span>
      <span class="brand-name">Meridale Circle</span>
    </div>
    <p class="disclosure">Advisory services offered through Stonebrook Assets, LLC</p>
  </section>

  <section class="card card-front" aria-label="Card front">
    <div class="holder">
      <h1 class="holder-name">Tobias L. Fenwright, MBA</h1>
      <p class="holder-title">Founder/President</p>
    </div>

    <div class="contact-band">
      <ul class="contact-list">
        <li>
          <svg viewBox="0 0 16 16" aria-hidden="true"><path fill="#fff" d="M3.5 1.5l2.5 3-1.5 1.5c1 2 3.5 4.5 5.5 5.5L11.5 10l3 2.5-1.5 2.5C7.5 14.5 1.5 8.5 1 3z"/></svg>
          (402) 555-0147
        </li>
        <li>
          <svg viewBox="0 0 16 16" aria-hidden="true"><rect x="4" y="1" width="8" height="14" rx="1.5" fill="none" stroke="#fff" stroke-width="1.6"/><circle cx="8" cy="12.5" r="1" fill="#fff"/></svg>
          (402) 555-0183
        </li>
        <li>
          <svg viewBox="0 0 16 16" aria-hidden="true"><rect x="4" y="1.5" width="8" height="4" fill="#fff"/><rect x="1.5" y="6" width="13" height="6" rx="1" fill="#fff"/><rect x="4" y="11" width="8" height="3.5" fill="#fff"/></svg>
          (402) 555-0129
        </li>
        <li>
          <svg viewBox="0 0 16 16" aria-hidden="true"><rect x="1.5" y="3.5" width="13" height="9" fill="none" stroke="#fff" stroke-width="1.4"/><path d="M1.5 3.5L8 9l6.5-5.5" fill="none" stroke="#fff" stroke-width="1.4"/></svg>
          tobias@meridaleplan.example
        </li>
        <li>
          <svg viewBox="0 0 16 16" aria-hidden="true"><circle cx="8" cy="8" r="6.5" fill="none" stroke="#fff" stroke-width="1.4"/><path d="M1.5 8h13M8 1.5c-3 3.5-3 9.5 0 13M8 1.5c3 3.5 3 9.5 0 13" fill="none" stroke="#fff" stroke-width="1.2"/></svg>
          www.meridaleplan.example
        </li>
      </ul>
    </div>

    <div class="front-brand">
      <span class="brand-dot"></span>
      <span class="brand-name">MERIDALE CIRCLE</span>
    </div>

    <p class="address">5287 E. Larkin Road, Suite 410, Harlow, NE 68190</p>
  </section>

</main>
</body>
</html>
```